Simple Business Card Design for Tavlo

Job:

Make a very simple, minimalist business card design with my details including adjusted logo. One side to be white (with logo & text). Other side to be yellow - try plain or with logo (or part of logo eg Z). Need business card to have continuity with website.

Logo:
Our logo is made from a free download font website:
http://www.typewell.net/search.php?q=rubber
but the spacing/kerning needs correcting/adjusting as the font spaces unevenly between letters (see attached files). Need logo to be very crisp/sharp when printed.

Printing:
We will be using Plika.com so the design needs to conform to their requirements, see here:

http://uk.plika.com/products/luxe/business-cards.html (scroll down for dimensions and guidelines)

Design:

must say "plant-based food consulting" underneath logo or somewhere
no address needed in contact section
sharp corners (not rounded)
one side white, one side yellow

name: Rosalind Whitcombe
1xmobile number: +44 7700900463
1xtwiiter: @brimcounsel
website address www.orchardtable.com
email address brim@orchardtable.com

Should be easy quick job, prompt + detailed feedback given, am online in UK 9am-10pm for next 3 days. Website is www.orchardtable.com

Industry/Entity Type

Business

Requirements
Must have
• The logo must be corrected. The kerning is not right.

Please use a warm-grey for text

Please submit in matt format, we will be printing matt finish.

Should not have
• Avoid using banners or curvy highlights

Please avoid using black

Please avoid submitting in gloss finish

```html
<!DOCTYPE html>
<html lang="en">
<head>
<meta charset="utf-8">
<title>BRIM business cards</title>
<link rel="stylesheet" href="https://fonts.googleapis.com/css2?family=Cinzel:wght@400;700&display=swap">
<style>
  :root {
    --backdrop: #e4e4e4;
    --card-white: #fbfaf7;
    --card-yellow: #ece35b;
    --accent: #ece35b;
    --warm-grey: #6e6760;
    --warm-grey-soft: #8c857d;
    --rule: #cfcac3;
    --band-light: #e2ddd5;
  }
  * { margin: 0; padding: 0; box-sizing: border-box; }
  html, body {
    width: 1200px; height: 720px; overflow: hidden;
    background: var(--backdrop);
    font-family: "Cinzel", serif;
  }
  .stage { position: relative; width: 1200px; height: 720px; }
  .card {
    position: absolute; top: 242px; width: 420px; height: 238px;
    overflow: hidden;
  }
  .card--front { left: 147px; background: var(--card-white); }
  .card--back { left: 633px; background: var(--card-yellow); }

  .brand-name {
    position: absolute; color: var(--warm-grey);
    font-weight: 700; line-height: 1; letter-spacing: 0.04em;
  }
  .card--front .brand-name { right: 18px; top: 28px; font-size: 50px; }
  .card--back .brand-name {
    left: 0; right: 0; top: 84px; text-align: center; font-size: 68px;
  }

  .tagline {
    position: absolute; right: 18px; top: 84px;
    color: var(--warm-grey-soft); font-size: 8.5px; letter-spacing: 0.08em;
  }

  .holder { position: absolute; left: 22px; top: 105px; }
  .holder__name { color: var(--warm-grey); font-weight: 700; font-size: 13px; line-height: 1.1; }
  .holder__role { color: var(--warm-grey-soft); font-size: 9.5px; line-height: 1.3; }

  .divider {
    position: absolute; left: 22px; top: 142px; width: 378px; height: 1px;
    background: var(--rule);
  }

  .contacts { position: absolute; left: 22px; top: 154px; list-style: none; }
  .contacts li {
    display: flex; align-items: center; height: 12px;
    color: var(--warm-grey); font-size: 8.5px; letter-spacing: 0.01em;
  }
  .contacts svg { width: 10px; height: 9px; margin-right: 8px; fill: var(--warm-grey); }

  .edge-band { position: absolute; left: 0; bottom: 0; width: 420px; height: 18px; }
</style>
</head>
<body>
<main class="stage">
  <section class="card card--front" aria-label="Card front">
    <div class="brand-name">BRIM</div>
    <p class="tagline">plant-based food consulting</p>
    <div class="holder">
      <p class="holder__name">Maren Holt</p>
      <p class="holder__role">Manager</p>
    </div>
    <div class="divider"></div>
    <ul class="contacts">
      <li>
        <svg viewBox="0 0 10 9"><path d="M0 3 Q5 0 10 3 L8.5 4 L7 3 L3 3 L1.5 4 Z M2 4.5 H8 L9 9 H1 Z"/></svg>
        +44 7700 900463
      </li>
      <li>
        <svg viewBox="0 0 10 9"><path d="M0 1 H10 V8 H0 Z M1 2 L5 5 L9 2" stroke="#fbfaf7" stroke-width="0.9"/></svg>
        brim@orchardtable.com
      </li>
      <li>
        <svg viewBox="0 0 10 9"><path d="M0 0.5 H10 V6.5 H0 Z M1.2 1.6 V5.4 H8.8 V1.6 Z M3.5 7.5 H6.5 V8.5 H3.5 Z"/></svg>
        www.orchardtable.com
      </li>
      <li>
        <svg viewBox="0 0 10 9"><circle cx="5" cy="4.5" r="4"/></svg>
        @brimcounsel
      </li>
    </ul>
    <svg class="edge-band" viewBox="0 0 420 18" preserveAspectRatio="none">
      <polygon points="0,10 263,10 260,18 0,18" fill="var(--band-light)"/>
      <polygon points="275,0 287,0 277,18 265,18" fill="var(--accent)"/>
      <polygon points="295,0 420,0 420,18 285,18" fill="var(--accent)"/>
    </svg>
  </section>

  <section class="card card--back" aria-label="Card back">
    <div class="brand-name">BRIM</div>
  </section>
</main>
</body>
</html>
```